Business Card Design Project - del varosi group

dear Sirs

we need business card design for our group ( DEL Varosi Group ) , i have got the Logo design of our group from pixel harbor in previous , so all need details relating to our group i think available with you, as well as the the chosen logo design

we hope to provide us with business card logo that to be appropaite and satisfactory to us .

thanks

note : logo design of our group is attached .
Updates

Reason: please extend the deadline of my project for additional 15 days because i didn't received appropriate design for our gruop yet . kindly beaware that i have received 77 design till now , supossed to send me 200-250 design at least . thanks

Target Market(s)

contents

name : Kerem EL Nadiri

position : Operation Manager

Industry/Entity Type

Business

Requirements
Must have

• person name

group logo
Nice to have
• logo color matching with back background

```html
<!DOCTYPE html>
<html lang="en">
<head>
<meta charset="utf-8">
<title>DEL Varosi Group – Business Cards</title>
<link rel="stylesheet" href="https://fonts.googleapis.com/css2?family=Questrial&family=Arimo:wght@400&display=swap">
<style>
  :root {
    --bg: #efe7d2;
    --navy: #163f7d;
    --navy-deep: #0d2f63;
    --navy-light: #2458a3;
    --gold: #c9a23a;
    --gold-text: #d4aa3c;
    --ink: #2b2b2b;
    --paper: #ffffff;
    --paper-shade: #e9eaee;
  }
  * { box-sizing: border-box; margin: 0; padding: 0; }
  html, body { width: 1200px; height: 951px; overflow: hidden; }
  body {
    background: var(--bg);
    font-family: "Arimo", Arial, sans-serif;
    position: relative;
  }
  .card {
    position: absolute;
    width: 640px;
    height: 366px;
    border-radius: 20px;
    overflow: hidden;
    box-shadow: 0 6px 18px rgba(60, 45, 20, 0.25);
  }
  /* Front */
  .card-front {
    left: 110px;
    top: 70px;
    background: radial-gradient(ellipse at 45% 40%, var(--navy-light) 0%, var(--navy) 45%, var(--navy-deep) 100%);
    display: flex;
    flex-direction: column;
    align-items: center;
    justify-content: center;
  }
  .brand {
    display: flex;
    align-items: center;
    gap: 16px;
    font-family: "Questrial", sans-serif;
    letter-spacing: 1px;
  }
  .brand-mark {
    width: 22px;
    height: 22px;
    background: var(--gold);
  }
  .card-front .brand { font-size: 46px; color: var(--paper); }
  .front-web {
    margin-top: 40px;
    font-family: "Questrial", sans-serif;
    color: var(--gold-text);
    font-size: 21px;
    letter-spacing: 2px;
  }
  /* Back */
  .card-back {
    left: 450px;
    top: 500px;
    background: linear-gradient(180deg, var(--paper) 0%, var(--paper) 60%, var(--paper-shade) 100%);
  }
  .back-panel { position: absolute; inset: 0; }
  .card-back .brand {
    position: absolute;
    left: 48px;
    top: 40px;
    font-size: 34px;
    color: var(--navy);
  }
  .card-back .brand-mark { width: 16px; height: 16px; }
  .contact {
    position: absolute;
    left: 48px;
    top: 120px;
    list-style: none;
    color: var(--ink);
    font-size: 17px;
    line-height: 1.3;
  }
  .contact li { display: flex; align-items: flex-start; gap: 10px; margin-bottom: 3px; }
  .contact svg { width: 15px; height: 15px; flex: none; margin-top: 2px; fill: var(--gold); }
  .contact .hl { color: var(--gold); }
  .person {
    position: absolute;
    right: 36px;
    bottom: 36px;
    text-align: left;
    font-family: "Questrial", sans-serif;
  }
  .person-name { color: var(--gold-text); font-size: 22px; letter-spacing: 0.5px; }
  .person-role { color: var(--paper); font-size: 17px; margin-top: 6px; letter-spacing: 0.5px; }
</style>
</head>
<body>

<section class="card card-front" aria-label="Card front">
  <div class="brand"><span class="brand-mark"></span><span class="brand-name">DEL VAROSI GROUP</span></div>
  <p class="front-web">www.delvarosigroup.com</p>
</section>

<section class="card card-back" aria-label="Card back">
  <svg class="back-panel" viewBox="0 0 640 366" preserveAspectRatio="none" aria-hidden="true">
    <path d="M478 0 C455 150 390 290 228 366 L640 366 L640 0 Z" fill="var(--gold)"/>
    <path d="M500 0 C478 150 418 292 262 366 L640 366 L640 0 Z" fill="var(--navy)"/>
  </svg>

  <div class="brand"><span class="brand-mark"></span><span class="brand-name">DEL VAROSI GROUP</span></div>

  <ul class="contact">
    <li>
      <svg viewBox="0 0 16 16"><path d="M8 1 L15 8 H13 V15 H10 V10 H6 V15 H3 V8 H1 Z"/></svg>
      <span>4100 Mill Crest Ave.<br>Suite 210-118<br>Dorval, TX 78104</span>
    </li>
    <li>
      <svg viewBox="0 0 16 16"><path d="M4 1 L6.5 4.5 L5 6.5 C6 8.5 7.5 10 9.5 11 L11.5 9.5 L15 12 L13 15 C7 14.5 1.5 9 1 3 Z"/></svg>
      <span>512-555-0142</span>
    </li>
    <li>
      <svg viewBox="0 0 16 16"><path d="M4 1 H11 V5 H4 Z M1 6 H15 V13 H12 V15 H4 V13 H1 Z M5 11 V14 H11 V11 Z"/></svg>
      <span>512-555-0143</span>
    </li>
    <li>
      <svg viewBox="0 0 16 16"><path d="M1 3 H15 V13 H1 Z M2 4 L8 9 L14 4 Z" fill-rule="evenodd"/></svg>
      <span>info@<span class="hl">delvarosigroup</span>.com</span>
    </li>
    <li>
      <svg viewBox="0 0 16 16"><circle cx="8" cy="8" r="7"/></svg>
      <span>www.<span class="hl">delvarosigroup</span>.com</span>
    </li>
  </ul>

  <div class="person">
    <p class="person-name">Kerem EL Nadiri</p>
    <p class="person-role">Operation Manager</p>
  </div>
</section>

</body>
</html>
```